Business Card for a Dental Office

The design should communicate integrity, quality and reliability. We also want the card look elegant, simple, but still stand out, different from the traditional-dental-office business card.

Industry/Entity Type

Business

```html
<!DOCTYPE html>
<html lang="en">
<head>
<meta charset="utf-8">
<title>Harlow Dental Centre – Business Card</title>
<link rel="stylesheet" href="https://fonts.googleapis.com/css2?family=Source+Sans+3:wght@400;600;700&display=swap">
<style>
  :root {
    --stage: #3b3330;
    --paper: #ffffff;
    --ink: #1c1c1c;
    --gold: #c8b21c;
    --gold-deep: #a8920e;
    --gold-light: #ddc940;
    --rule: #6a6a6a;
    --faint: #ececec;
  }
  * { box-sizing: border-box; margin: 0; padding: 0; }
  html, body { width: 1200px; height: 844px; overflow: hidden; }
  body {
    background: var(--stage);
    font-family: "Source Sans 3", "Helvetica Neue", Arial, sans-serif;
    color: var(--ink);
    position: relative;
  }
  .card {
    position: absolute;
    top: 279px;
    width: 510px;
    height: 286px;
    background: var(--paper);
    overflow: hidden;
    box-shadow: 0 10px 30px rgba(0,0,0,.45);
  }
  .card--front { left: 60px; }
  .card--back { left: 630px; }

  /* Front */
  .brand {
    position: absolute;
    top: 58px;
    left: 150px;
    display: flex;
    align-items: center;
    gap: 12px;
  }
  .brand__mark { width: 46px; height: 46px; background: var(--ink); }
  .brand__text { display: flex; flex-direction: column; }
  .brand__name {
    font-weight: 700;
    font-size: 24px;
    letter-spacing: .5px;
    text-transform: uppercase;
    line-height: 1;
    color: var(--ink);
  }
  .brand__tagline {
    margin-top: 4px;
    font-weight: 600;
    font-size: 11.5px;
    letter-spacing: 1px;
    text-transform: uppercase;
    color: var(--gold);
  }
  .contact {
    position: absolute;
    left: 30px;
    bottom: 26px;
    font-size: 13.5px;
    line-height: 1.35;
  }
  .contact__name { color: var(--gold); font-weight: 600; font-size: 16px; }
  .contact__role { margin-bottom: 14px; }
  .contact__address { margin-bottom: 14px; }
  .contact__label { color: var(--gold); }
  .contact__web { color: var(--gold); margin-left: 10px; }
  .contact__row span + span { margin-left: 8px; }

  /* Back */
  .appt__band {
    position: absolute;
    top: 0; left: 0; right: 0;
    height: 62px;
    background: linear-gradient(180deg, var(--gold-light), var(--gold-deep));
  }
  .appt__title {
    position: absolute;
    top: 18px;
    left: 170px;
    font-weight: 600;
    font-size: 18px;
    color: var(--ink);
  }
  .appt__logo {
    position: absolute;
    top: 26px;
    left: 28px;
    width: 112px;
    height: 78px;
    background: var(--paper);
    display: flex;
    flex-direction: column;
    align-items: center;
    justify-content: center;
    gap: 6px;
  }
  .appt__logo .brand__mark { width: 26px; height: 26px; }
  .appt__logo .brand__name { font-size: 11px; text-align: center; line-height: 1.1; }
  .appt__decor {
    position: absolute;
    right: -30px;
    top: 70px;
    width: 160px;
    height: 160px;
    background: var(--faint);
  }
  .appt__form {
    position: absolute;
    top: 84px;
    left: 170px;
    right: 40px;
    font-size: 13px;
    font-weight: 600;
  }
  .field {
    display: flex;
    align-items: flex-end;
    gap: 6px;
    height: 30px;
  }
  .field__line { flex: 1; border-bottom: 1.5px dotted var(--rule); height: 12px; }
  .field__unit { font-size: 11px; }
  .appt__note {
    position: absolute;
    left: 170px;
    bottom: 34px;
    font-size: 14px;
    font-weight: 600;
    line-height: 1.35;
  }
</style>
</head>
<body>
  <section class="card card--front" aria-label="Business card front">
    <div class="brand">
      <div class="brand__mark" aria-hidden="true"></div>
      <div class="brand__text">
        <span class="brand__name">Harlow Dental Centre</span>
        <span class="brand__tagline">Your smile is your gift to others</span>
      </div>
    </div>
    <div class="contact">
      <p class="contact__name">John Smith</p>
      <p class="contact__role">Managing Director</p>
      <p class="contact__address">1234, Address GoesHere, Country, 12345</p>
      <p class="contact__row">
        <span><span class="contact__label">T:</span>(044) 123 456 789</span>
        <span><span class="contact__label">F:</span>(044) 123456789</span>
        <span><span class="contact__label">M:</span>(044)123456789</span>
      </p>
      <p class="contact__row">
        <span><span class="contact__label">E:</span>info@youremail.com</span>
        <span class="contact__web">www.yourweb.com</span>
      </p>
    </div>
  </section>

  <section class="card card--back" aria-label="Appointment card back">
    <div class="appt__band"></div>
    <div class="appt__decor" aria-hidden="true"></div>
    <h2 class="appt__title">Your Next Appointment is</h2>
    <div class="appt__logo">
      <div class="brand__mark" aria-hidden="true"></div>
      <span class="brand__name">Harlow Dental<br>Centre</span>
    </div>
    <div class="appt__form">
      <div class="field"><span>Name :</span><span class="field__line"></span></div>
      <div class="field"><span>Date :</span><span class="field__line"></span></div>
      <div class="field">
        <span>Time :</span><span class="field__line"></span><span class="field__unit">AM</span>
        <span class="field__line"></span><span class="field__unit">PM</span>
      </div>
    </div>
    <p class="appt__note">If unable to keep appointment,<br>kindly give 24hrs notice.</p>
  </section>
</body>
</html>
```